Hollow Meridian Book website design.

This is a simple one-page web design for my book.
I have all files and video needed.
Domain listed with Net Harbor.
Password and username will be given to winning bid.
Domain address, www.hollowmeridian.info
Upload a 30 second video so it can be played on the website.
Book cover photo
Book Blurb text.
Links to Rivermart and Audio books where the book can be purchased.
Below is the link to the Rivermart listing.
https://www.rivermart.example/dp/X00AAAAAA1/?coliid=QWERTYUIOPASD&colid=1ZXCVBNMLKJH0&psc=0&ref_=lv_ov_lig_dp_i
Below is the link to my Listenly books.com listing.
https://www.listenly.example/pd/Hollow-Meridian-Audiobook/X00BBBBBB2?qid=1000000001&sr=1-7&ref=a_search_c3_lProduct_1_7&pf_rd_p=00000000-aaaa-bbbb-cccc-000000000000&pf_rd_r=ZZZZ00000000000000QQ
Text on page.” Click on either logo to go directly to Rivermart or Listenly.com
Link Listenly book logo to my book on Listenly.com
Place this text under Listenly.com logo: “Free to new members of Listenly.com”
Link Rivermart logo to my book on Rivermart.
Place this text under Rivermart logo “ Free to new Pagewisp members on Rivermart.com”
Link the book photo to the Rivermart.com web address as well.
Enter meta tags or keywords below for search engines to locate webpage.
Hollow Meridian
Conspiracy
Conspiracy Books
Spy books
Thriller books
Suspense books
Comedy books
Dorian Welbeck

```html
<!DOCTYPE html>
<html lang="en">
<head>
<meta charset="utf-8">
<title>Hollow Meridian</title>
<meta name="keywords" content="Hollow Meridian, Conspiracy, Conspiracy Books, Spy books, Thriller books, Suspense books, Comedy books, Dorian Welbeck">
<link rel="stylesheet" href="https://fonts.googleapis.com/css2?family=Lora:wght@700&family=Roboto:wght@400;500;700&display=swap">
<style>
:root{
  --navy:#0b0b63;
  --red:#a5000f;
  --ink:#111111;
  --body:#555555;
  --footer:#181818;
  --white:#ffffff;
}
*{box-sizing:border-box;margin:0;padding:0}
html,body{width:678px;height:1200px;overflow:hidden;background:var(--white)}
body{position:relative;font-family:'Roboto',Arial,sans-serif;color:var(--ink)}
a{color:inherit;text-decoration:none}
.abs{position:absolute}
.serif{font-family:'Lora',Georgia,serif;font-weight:700}

/* header */
.site-header{position:absolute;left:0;top:0;width:678px;height:41px;background:var(--white);z-index:3}
.brand{left:63px;top:9px;font-size:16px}
.nav{top:16px;font-size:8px;font-weight:700;letter-spacing:.1px}
.btn{background:var(--navy);color:var(--white);border-radius:13px;font-weight:700;font-size:8px;display:flex;align-items:center;justify-content:center;gap:6px}
.btn .dot{width:8px;height:8px;border-radius:50%;background:var(--white);position:relative}
.btn .dot::after{content:"";position:absolute;left:3px;top:2px;border-left:3px solid var(--navy);border-top:2px solid transparent;border-bottom:2px solid transparent}

/* hero */
.hero-photo{left:0;top:40px;width:678px;height:370px;background:linear-gradient(180deg,#b9ab9a 0%,#8e7b64 25%,#4d4535 55%,#2f2c24 100%)}
.hero-shade{left:0;top:40px;width:678px;height:370px;background:rgba(0,0,0,.18)}
.hero-welcome{left:0;width:678px;top:129px;text-align:center;color:var(--white);font-size:15px}
.hero-title{left:0;width:678px;top:148px;text-align:center;color:var(--white);font-size:34px;line-height:40px}
.hero-text{left:60px;width:558px;top:198px;text-align:center;color:var(--white);font-size:9.6px;line-height:14.5px}
.play{left:339px;top:241px;width:23px;height:23px;border-radius:50%;background:rgba(255,255,255,.85);display:flex;align-items:center;justify-content:center}
.play span{width:15px;height:15px;border-radius:50%;background:var(--red);position:relative}
.play span::after{content:"";position:absolute;left:6px;top:4px;border-left:5px solid var(--white);border-top:3.5px solid transparent;border-bottom:3.5px solid transparent}
.watch{left:369px;top:248px;color:var(--white);font-size:8px;font-weight:700}

/* books */
.books-bg{left:0;top:420px;width:678px;height:528px;background:linear-gradient(160deg,#f3f3f6 0%,#ffffff 35%,#f7eeee 60%,#ffffff 80%,#f2f2f5 100%)}
.cover{background:linear-gradient(160deg,#3b3b5a 0%,#7a1018 40%,#111 75%,#000 100%)}
.store-name{font-size:22px;font-weight:700;color:var(--ink);display:flex;align-items:center;gap:6px}
.store-name i{display:inline-block;width:10px;height:10px;background:var(--navy)}
.free{font-size:7.6px;font-weight:500;color:#333}
.book-title{font-size:12px;font-weight:500;color:var(--ink)}
.blurb{font-size:8.3px;line-height:14px;color:var(--body);text-align:justify}
.go{font-size:8px;font-weight:500;color:var(--navy);border-bottom:1px solid var(--navy);display:flex;align-items:center;gap:6px;padding-bottom:1px}
.go .dot{width:7px;height:7px;border-radius:50%;background:var(--navy);position:relative}
.go .dot::after{content:"";position:absolute;left:2.6px;top:1.7px;border-left:2.6px solid var(--white);border-top:1.8px solid transparent;border-bottom:1.8px solid transparent}

/* footer */
.footer-bg{left:0;top:1000px;width:678px;height:172px;background:var(--footer)}
.footer-brand{left:61px;top:1054px;font-size:15px;color:var(--white)}
.social{top:1083px;width:20px;height:20px;border:1px solid #cfcfcf;border-radius:50%}
.col-title{font-size:8px;font-weight:700;color:var(--white);padding-bottom:8px;border-bottom:1px solid #bdbdbd}
.links{list-style:none;font-size:8.3px;color:var(--white)}
.links li{height:19.5px;display:flex;align-items:center;gap:9px}
.links li::before{content:"»";font-size:9px;width:7px}
.news-text{left:434px;top:1053px;font-size:8.3px;color:var(--white)}
.email{left:434px;top:1075px;width:161px;height:27px;background:var(--white);border-radius:2px;font-size:8.3px;color:#666;padding:9px 10px}
.send{left:571px;top:1076px;width:23px;height:25px;background:var(--navy);display:flex;align-items:center;justify-content:center}
.copyright{left:0;top:1170px;width:678px;height:30px;background:var(--red);color:var(--white);font-size:8.3px;text-align:center;line-height:30px}
</style>
</head>
<body>

<header class="site-header">
  <a class="abs brand serif" href="#">Hollow Meridian</a>
  <a class="abs nav" style="left:326px" href="#">HOME</a>
  <a class="abs nav" style="left:366px" href="#">ABOUT</a>
  <a class="abs nav" style="left:409px" href="#">MY BOOKS</a>
  <a class="abs nav" style="left:467px" href="#">CONTACT</a>
  <a class="abs btn" style="left:525px;top:8px;width:89px;height:24px" href="#">GET STARTED <span class="dot"></span></a>
</header>

<section>
  <div class="abs hero-photo" role="img" aria-label="Aerial view of the capital city skyline at sunset"></div>
  <div class="abs hero-shade"></div>
  <h2 class="abs hero-welcome serif">Welcome to</h2>
  <h1 class="abs hero-title serif">Hollow Meridian</h1>
  <p class="abs hero-text">Lorem ipsum dolor sit amet, consectetur adipiscing elit, sed do eiusmod tempor incididunt ut labore et dolore magna aliqua. Ut enim ad minim veniam, quis nostrud exercitation ullamco laboris nisi ut aliquip ex ea commodo</p>
  <a class="abs btn" style="left:237px;top:240px;width:89px;height:24px" href="#">GET STARTED <span class="dot"></span></a>
  <a class="abs play" href="#"><span></span></a>
  <a class="abs watch" href="#">WATCH OUR VIDEO</a>
  <svg class="abs" style="left:0;top:340px" width="678" height="80" viewBox="0 0 678 80" aria-hidden="true">
    <path d="M0 40 C80 0 160 10 260 32 C360 52 440 10 540 40 C600 58 640 60 678 18 L678 80 L0 80 Z" fill="var(--navy)"/>
    <path d="M0 44 C80 6 160 16 260 38 C360 58 440 16 540 46 C600 64 640 66 678 24 L678 80 L0 80 Z" fill="var(--red)"/>
    <path d="M0 50 C80 14 160 24 260 44 C360 62 440 22 540 52 C600 70 640 72 678 32 L678 80 L0 80 Z" fill="var(--white)"/>
  </svg>
</section>

<main>
  <div class="abs books-bg" role="img" aria-label="Faint waving national flag background"></div>

  <a class="abs cover" style="left:131px;top:435px;width:138px;height:221px" href="#" role="img" aria-label="Hollow Meridian book cover by Dorian Welbeck"></a>
  <a class="abs store-name" style="left:339px;top:456px" href="#"><i></i>Rivermart</a>
  <p class="abs free" style="left:339px;top:489px">Free to new Pagewisp members on Rivermart.com</p>
  <h3 class="abs book-title" style="left:339px;top:510px">Hollow Meridian Edición Pagewisp</h3>
  <p class="abs blurb" style="left:339px;top:531px;width:276px">Lorem ipsum dolor sit amet, consectetur adipiscing elit, sed do eiusmod tempor incididunt ut labore et dolore magna aliqua. Ut enim ad minim veniam, quis nostrud exercitation ullamco laboris nisi ut aliquip ex ea commodo consequat. Duis aute irure dolor in reprehenderit in voluptate velit esse cillum dolore eu fugiat nulla pariatur. Excepteur sint occaecat cupidatat non proident, sunt in culpa qui officia deserunt</p>
  <a class="abs go" style="left:339px;top:623px" href="#">CLICK TO GO DIRECTLY TO RIVERMART.COM <span class="dot"></span></a>

  <a class="abs store-name" style="left:62px;top:735px" href="#"><i></i>Listenly</a>
  <p class="abs free" style="left:62px;top:770px">Free to new members of Listenly.com</p>
  <h3 class="abs book-title" style="left:62px;top:791px">Hollow Meridian</h3>
  <p class="abs blurb" style="left:62px;top:812px;width:277px">Lorem ipsum dolor sit amet, consectetur adipiscing elit, sed do eiusmod tempor incididunt ut labore et dolore magna aliqua. Ut enim ad minim veniam, quis nostrud exercitation ullamco laboris nisi ut aliquip ex ea commodo consequat. Duis aute irure dolor in reprehenderit in voluptate velit esse cillum dolore eu fugiat nulla pariatur. Excepteur sint occaecat cupidatat non proident, sunt in culpa qui officia deserunt</p>
  <a class="abs go" style="left:62px;top:904px" href="#">CLICK &nbsp;TO GO DIRECTLY TO &nbsp;LISTENLY.COM <span class="dot"></span></a>

  <a class="abs cover" style="left:394px;top:735px;width:174px;height:183px;background:linear-gradient(180deg,#000 0%,#000 42%,#2a2a3a 60%,#6a0f16 85%,#000 100%)" href="#" role="img" aria-label="Audiobook cover for Hollow Meridian by Dorian Welbeck"></a>
</main>

<footer>
  <svg class="abs" style="left:0;top:950px" width="678" height="60" viewBox="0 0 678 60" aria-hidden="true">
    <path d="M0 40 C70 0 150 8 250 32 C350 52 440 20 540 30 C610 38 650 30 678 12 L678 60 L0 60 Z" fill="var(--red)"/>
    <path d="M0 46 C70 6 150 14 250 38 C350 58 440 26 540 36 C610 44 650 36 678 18 L678 60 L0 60 Z" fill="var(--navy)"/>
    <path d="M0 52 C70 14 150 22 250 44 C350 62 440 32 540 42 C610 50 650 42 678 26 L678 60 L0 60 Z" fill="var(--footer)"/>
  </svg>
  <div class="abs footer-bg"></div>
  <a class="abs footer-brand serif" href="#">Hollow Meridian</a>
  <a class="abs social" style="left:88px" href="#" aria-label="Social profile one"></a>
  <a class="abs social" style="left:113px" href="#" aria-label="Social profile two"></a>
  <a class="abs social" style="left:137px" href="#" aria-label="Social profile three"></a>
  <a class="abs social" style="left:162px" href="#" aria-label="Social profile four"></a>

  <h4 class="abs col-title" style="left:232px;top:1024px;width:157px">LINKS</h4>
  <ul class="abs links" style="left:232px;top:1048px">
    <li>Home</li><li>About us</li><li>My Books</li><li>Testimonials</li><li>Portfolio</li>
  </ul>
  <ul class="abs links" style="left:329px;top:1048px">
    <li>Our Team</li><li>Sitemap</li><li>Privacy Policy</li><li>Terms Of Use</li><li>Contact Us</li>
  </ul>

  <h4 class="abs col-title" style="left:433px;top:1024px;width:158px">NEWSLETTER</h4>
  <p class="abs news-text">Send us a newsletter to get update</p>
  <div class="abs email">Email Address</div>
  <a class="abs send" href="#" aria-label="Subscribe">
    <svg width="10" height="10" viewBox="0 0 10 10"><path d="M9.5 .5 L.5 4.5 L4 5.8 L5.3 9.5 Z M9.5 .5 L4 5.8" fill="none" stroke="#fff" stroke-width="1" stroke-linejoin="round"/></svg>
  </a>
  <div class="abs copyright">© 2022 Hollow Meridian. All Rights Reserved</div>
</footer>

</body>
</html>
```